Verdant Systems Business Card

want the back of card to be blue- with the logo in the center
front of card- info plus logo (info being mailing address, email address, and website address )
4 different names with titles to have on cards
1) Calvin Borsted - Owner
2) Naomi Trelvik- Customer Relationship Specialist
3) Felix Andrade- Vice President of Sales
4) Owen Markby- Chief Technology Officer

Target Market(s)

tech company in the government/probation office industry

Industry/Entity Type

Government Office

Contact Information for Business Card

1) Calvin Borsted - Owner

Colors
0355a3
ffffff

Requirements
Must have
• back side should be blue, with the logo placed in the center
• front side needs to include both the logo, as well as company info (info should include website address, email address, and mailing address)

```html
<!DOCTYPE html>
<html lang="en">
<head>
<meta charset="utf-8">
<title>Verdant Systems Business Card</title>
<link rel="stylesheet" href="https://fonts.googleapis.com/css2?family=Open+Sans:wght@400;600;700&display=swap">
<style>
  :root {
    --navy: #1b2d55;
    --grey: #898a8e;
    --fold: #4d4e52;
    --white: #ffffff;
    --backdrop: #3a3b3e;
  }
  html, body {
    margin: 0;
    padding: 0;
    width: 1200px;
    height: 900px;
    overflow: hidden;
    background: var(--backdrop);
    font-family: "Open Sans", sans-serif;
  }
  .card {
    position: absolute;
    left: 290px;
    width: 620px;
    height: 354px;
    border-radius: 22px;
    overflow: hidden;
  }
  .card-back {
    top: 60px;
    background: var(--navy);
    display: flex;
    align-items: center;
    justify-content: center;
  }
  .card-back .brand-name {
    color: var(--white);
    font-size: 40px;
    font-weight: 600;
    letter-spacing: 1px;
  }
  .card-front {
    top: 486px;
    background: var(--white);
  }
  .card-front .shapes {
    position: absolute;
    inset: 0;
  }
  .front-brand {
    position: absolute;
    left: 0;
    top: 140px;
    width: 248px;
    text-align: center;
    color: var(--navy);
    font-size: 24px;
    font-weight: 600;
  }
  .holder {
    position: absolute;
    left: 262px;
    top: 52px;
    color: var(--white);
  }
  .holder-name {
    font-size: 20px;
    font-weight: 700;
    line-height: 1.2;
  }
  .holder-title {
    font-size: 15px;
    font-weight: 400;
    padding-left: 18px;
  }
  .contacts {
    position: absolute;
    left: 360px;
    top: 158px;
    margin: 0;
    padding: 0;
    list-style: none;
    color: var(--white);
    font-size: 14px;
    line-height: 22px;
  }
  .contacts li {
    display: flex;
    align-items: center;
    gap: 9px;
  }
  .contacts svg {
    width: 12px;
    height: 12px;
    flex: none;
  }
  .address {
    position: absolute;
    left: 24px;
    top: 276px;
    height: 42px;
    line-height: 42px;
    color: var(--white);
    font-size: 15px;
  }
</style>
</head>
<body>

<section class="card card-back" aria-label="Card back">
  <span class="brand-name">Verdant Systems</span>
</section>

<section class="card card-front" aria-label="Card front">
  <svg class="shapes" viewBox="0 0 620 354" width="620" height="354" aria-hidden="true">
    <polygon points="248,0 620,0 620,354 428,354 428,262 248,262" fill="var(--navy)"/>
    <polygon points="229,50 484,50 484,106 229,106" fill="var(--grey)"/>
    <polygon points="248,106 266,106 248,120" fill="var(--fold)"/>
    <polygon points="410,262 428,262 428,276" fill="var(--fold)"/>
    <polygon points="0,276 428,276 428,318 0,318" fill="var(--grey)"/>
  </svg>

  <div class="front-brand">Verdant Systems</div>

  <div class="holder">
    <div class="holder-name">Calvin Borsted</div>
    <div class="holder-title">Owner</div>
  </div>

  <ul class="contacts">
    <li>
      <svg viewBox="0 0 12 12"><path d="M2.5 1l2 2.2-1.2 1.3c.7 1.6 1.9 2.8 3.5 3.5L8 6.8 10.2 8.8 9 11C4.6 10.6 1.4 7.4 1 3z" fill="var(--white)"/></svg>
      <span>404-221-7386</span>
    </li>
    <li>
      <svg viewBox="0 0 12 12"><rect x="3" y="0.8" width="6" height="10.4" rx="1" fill="none" stroke="var(--white)" stroke-width="1.2"/><circle cx="6" cy="9.4" r="0.7" fill="var(--white)"/></svg>
      <span>404-317-5820(office)</span>
    </li>
    <li>
      <svg viewBox="0 0 12 12"><rect x="0.8" y="2.2" width="10.4" height="7.6" fill="none" stroke="var(--white)" stroke-width="1.2"/><path d="M0.8 2.4L6 6.6 11.2 2.4" fill="none" stroke="var(--white)" stroke-width="1.2"/></svg>
      <span>calvin@verdantsystems.net</span>
    </li>
    <li>
      <svg viewBox="0 0 12 12"><circle cx="6" cy="6" r="5" fill="none" stroke="var(--white)" stroke-width="1.2"/><path d="M1 6h10M6 1c-2 2.6-2 7.4 0 10M6 1c2 2.6 2 7.4 0 10" fill="none" stroke="var(--white)" stroke-width="1"/></svg>
      <span>www.verdantsystems.net</span>
    </li>
  </ul>

  <div class="address">Harrow Lane Fenwick Park Ashford, 2047</div>
</section>

</body>
</html>
```